Web site for radio show

I've got a radio show starting on OrbitalWave and need a web site for it. I am familiar with WordPress, so I'd like to get a design for a WordPress-based web site for the show.

I'm also posting a logo project to be done at the same time.

The best radio show web site I've seen is the Cosmic Tuesday site (www.cosmictuesday-example.com). That's a good model but I don't want to start with that much complexity and content. The initial site that I'd like you to design would have the following parts:
- Upcoming shows
- Past shows (including links to authors, their web sites, and their books)
- Chirp Feed
- Blog
- About
- ...and anything else you think would be necessary

For colors, I'd like it to be consistent with my personal web site: www.kellaway-ventures-example.com

Target Market(s)

The target market for this show is mid- to upper-level managers

Industry/Entity Type

Radio

Requirements
Must have
• The project has to proceed in (at least) two stages: a first rough layout, and a second finished design. Whether you want a third stage in between with look and feel options is up to you.

```html
<!DOCTYPE html>
<html lang="en">
<head>
<meta charset="utf-8">
<title>Kellaway Show</title>
<link href="https://fonts.googleapis.com/css2?family=Ubuntu:wght@300;400;500;700&display=swap" rel="stylesheet">
<style>
:root{
  --red:#c8161d;
  --red-dark:#b10f16;
  --red-light:#dc3a3c;
  --ink:#3a3a3a;
  --muted:#6a6a6a;
  --soft:#9a9a9a;
  --line:#d9d9d9;
  --panel:#f4f4f4;
  --cyan:#4cc8ea;
  --white:#fff;
}
*{box-sizing:border-box;margin:0;padding:0}
html,body{width:994px;height:1200px;overflow:hidden;background:var(--white);font-family:"Ubuntu",sans-serif;color:var(--ink)}
.page{position:absolute;left:75px;top:0;width:850px;height:1200px;background:var(--white);box-shadow:0 0 4px rgba(0,0,0,.12);overflow:hidden}
.abs{position:absolute}
/* header */
.brand{left:25px;top:26px;font-size:30px;font-weight:500;color:var(--red);letter-spacing:-.3px}
.brand span{color:#9b9b9b}
.slogan{left:27px;top:60px;font-size:11px;color:var(--soft)}
.social{top:19px;width:22px;height:22px;border-radius:50%;background:#9d9d9d}
.search{left:633px;top:16px;width:193px;height:25px;border:1px solid var(--line);font-size:10px;font-style:italic;color:#999;padding:6px 10px}
.search svg{position:absolute;right:8px;top:5px}
.nav{top:59px;font-size:13px;font-weight:500;color:#555}
.nav a{position:absolute;white-space:nowrap;text-decoration:none;color:inherit}
.nav a.on{color:var(--red)}
/* hero */
.hero{left:0;top:94px;width:850px;height:323px;background:linear-gradient(180deg,var(--red-light),var(--red) 60%,var(--red-dark))}
.hero-kicker{left:55px;top:72px;font-size:28px;font-weight:300;color:var(--white)}
.hero-title{left:55px;top:108px;font-size:36px;font-weight:500;color:var(--white)}
.hero-text{left:57px;top:154px;width:320px;font-size:11px;line-height:16.6px;color:var(--white)}
.dot{top:213px;width:10px;height:10px;border-radius:50%;background:rgba(255,255,255,.55)}
.dot.on{background:var(--white)}
.video{left:427px;top:40px;width:360px;height:231px;border:4px solid var(--white);border-radius:6px;background:radial-gradient(circle at 55% 45%,#e6e8ea,#b9bcc0 75%,#9fa3a8)}
.play{left:158px;top:95px;width:42px;height:42px;border-radius:50%;background:#1e1e1e;border:2px solid #ddd}
/* shows */
.sec-title{font-size:25px;font-weight:300;color:#444}
.show{width:380px;height:72px}
.thumb{position:absolute;left:0;top:0;width:114px;height:72px}
.show h3{position:absolute;left:127px;top:0;font-size:13px;font-weight:400;color:var(--red)}
.show p{position:absolute;left:127px;top:20px;width:242px;font-size:10px;line-height:18.3px;color:var(--muted)}
.divider{left:22px;top:759px;width:806px;height:5px;border-top:1px dotted #c9c9c9;border-bottom:1px dotted #c9c9c9}
/* boxes */
.box{top:797px;width:261px;height:282px;border:1px solid var(--line);border-radius:3px;overflow:hidden}
.box-head{height:43px;background:var(--panel);border-bottom:1px solid var(--line);font-size:21px;font-weight:300;color:#444;padding:10px 0 0 23px}
.box-head.chirp{background:linear-gradient(180deg,#7cd8f2,var(--cyan));color:var(--white);border-bottom:none}
.box-text{font-size:10px;line-height:18.3px;color:var(--muted)}
.blog h4{font-size:13px;font-weight:400;color:var(--red);margin-bottom:2px}
.blog p{margin-bottom:8px}
.tweet{left:21px;width:220px;height:60px}
.avatar{position:absolute;left:0;top:0;width:56px;height:50px;border-radius:3px}
.tweet p{position:absolute;left:68px;top:-5px;width:152px;font-size:10px;line-height:15.7px;color:var(--muted)}
.tweet b{font-weight:500;color:#444}
.tweet small{color:var(--soft);font-size:10px}
/* footer */
.footer{left:0;top:1111px;width:850px;height:89px;background:#f0f0f0;border-top:1px solid #e2e2e2}
.fnav{left:30px;top:25px;font-size:12px;font-weight:500;color:#333;word-spacing:1px}
.copy{left:30px;top:50px;font-size:11px;color:#777}
.partner{left:600px;top:29px;font-size:24px;font-weight:700;color:#1a3d7c}
</style>
</head>
<body>
<div class="page">
  <header>
    <div class="abs brand">Kellaway <span>Show</span></div>
    <div class="abs slogan">your slogan goes here</div>
    <div class="abs social" style="left:553px"></div>
    <div class="abs social" style="left:578px"></div>
    <div class="abs social" style="left:604px"></div>
    <div class="abs search">Search here..
      <svg width="14" height="14" viewBox="0 0 14 14"><circle cx="6" cy="6" r="4.5" fill="none" stroke="#888" stroke-width="1.8"/><line x1="9.3" y1="9.3" x2="13" y2="13" stroke="#888" stroke-width="2"/></svg>
    </div>
    <nav class="abs nav" style="left:0">
      <a class="on" style="left:310px">HOME</a>
      <a style="left:380px">ABOUT</a>
      <a style="left:455px">LISTEN</a>
      <a style="left:529px">SHOWS</a>
      <a style="left:608px">BLOG</a>
      <a style="left:675px">SUPPORT</a>
      <a style="left:765px">CONTACT</a>
    </nav>
  </header>

  <section class="abs hero">
    <div class="abs hero-kicker">Welcome to Mainpage of</div>
    <div class="abs hero-title">Kellaway Show</div>
    <p class="abs hero-text">Phasellus felis dolor scelerisque a tempus eget lobortis id libero Aliquam nec erat at purus cursus interdum Vestibulum ligula augue bibendum accumsan vestibulum</p>
    <div class="abs dot on" style="left:58px"></div>
    <div class="abs dot" style="left:72px"></div>
    <div class="abs dot" style="left:85px"></div>
    <div class="abs dot" style="left:98px"></div>
    <div class="abs video" role="img" aria-label="Studio microphone video still">
      <div class="abs play"><svg width="38" height="38" viewBox="0 0 38 38"><path d="M15 11 L27 19 L15 27 Z" fill="#fff"/></svg></div>
    </div>
  </section>

  <section>
    <h2 class="abs sec-title" style="left:37px;top:438px">Upcoming Shows</h2>
    <div class="abs show" style="left:35px;top:479px"><div class="thumb" role="img" aria-label="Jazz show artwork" style="background:linear-gradient(135deg,#3b2a9a,#a03a8c 60%,#e0a030)"></div><h3>Show tittle here</h3><p>Aliquam nec erat at purus cursus interdum Vestibu-lum ligula augue bibendum accumsan vestibulum ut commodo&nbsp; Morbi ornare</p></div>
    <div class="abs show" style="left:35px;top:566px"><div class="thumb" role="img" aria-label="Host at studio microphone" style="background:linear-gradient(135deg,#8c8c88,#c9b49a 60%,#6f6e6a)"></div><h3>Show tittle here</h3><p>Aliquam nec erat at purus cursus interdum Vestibu-lum ligula augue bibendum accumsan vestibulum ut commodo&nbsp; Morbi ornare</p></div>
    <div class="abs show" style="left:35px;top:654px"><div class="thumb" role="img" aria-label="On air studio host" style="background:linear-gradient(135deg,#1d5fa8,#2a3f6a 60%,#b08a6a)"></div><h3>Show tittle here</h3><p>Aliquam nec erat at purus cursus interdum Vestibu-lum ligula augue bibendum accumsan vestibulum ut commodo&nbsp; Morbi ornare</p></div>

    <h2 class="abs sec-title" style="left:450px;top:438px">Past Shows</h2>
    <div class="abs show" style="left:452px;top:479px"><div class="thumb" role="img" aria-label="Broadcast mixing desk" style="background:linear-gradient(135deg,#3c4a4a,#8aa0a0 55%,#2e3434)"></div><h3>Show tittle here</h3><p>Aliquam nec erat at purus cursus interdum Vestibu-lum ligula augue bibendum accumsan vestibulum ut commodo&nbsp; Morbi ornare</p></div>
    <div class="abs show" style="left:452px;top:566px"><div class="thumb" role="img" aria-label="Two hosts in studio" style="background:linear-gradient(135deg,#4a3a30,#c99a80 55%,#5a4a40)"></div><h3>Show tittle here</h3><p>Aliquam nec erat at purus cursus interdum Vestibu-lum ligula augue bibendum accumsan vestibulum ut commodo&nbsp; Morbi ornare</p></div>
    <div class="abs show" style="left:452px;top:654px"><div class="thumb" role="img" aria-label="Illuminated on air sign" style="background:linear-gradient(135deg,#3a0a04,#d23a10 50%,#f0c040)"></div><h3>Show tittle here</h3><p>Aliquam nec erat at purus cursus interdum Vestibu-lum ligula augue bibendum accumsan vestibulum ut commodo&nbsp; Morbi ornare</p></div>
  </section>

  <div class="abs divider"></div>

  <section class="abs box" style="left:22px">
    <div class="box-head">About Us</div>
    <div class="abs" role="img" aria-label="Host portrait in studio" style="left:19px;top:54px;width:89px;height:87px;border-radius:3px;background:linear-gradient(135deg,#2a4a7a,#c8a088 60%,#3a5a9a)"></div>
    <p class="abs box-text" style="left:118px;top:51px;width:122px">Morbi ornare gravida elit Integer congue augue et malesuada iaculis ipsum dui aliquet felis at cursus magna nisl nec elit Ves</p>
    <p class="abs box-text" style="left:19px;top:147px;width:228px">Morbi ornare gravida elit Integer congue augue et malesuada iaculis ipsum dui aliquet felis at cursus magna nisl nec elit<br>Vestibulum gravida Praesent elementum elit at tellus Malesuada nec ultricies sit amet</p>
  </section>

  <section class="abs box blog" style="left:294px">
    <div class="box-head">Recent Blog</div>
    <div class="abs box-text" style="left:23px;top:54px;width:205px">
      <h4>Morbi ornare gravida Integer</h4><p>congue augue et malesuada iaculis ipsum dui aliquet felis at cursus magna nisl nec</p>
      <h4>Suspendisse quam</h4><p>congue augue et malesuada iaculis ipsum dui aliquet felis at cursus magna nisl nec</p>
      <h4>Pellentesque faucibus</h4><p>Maecenas at justo id velit placerat molestie Donec dictum lectus non odio Cras a ante vitae enim iaculis aliquam</p>
    </div>
  </section>

  <section class="abs box" style="left:568px">
    <div class="box-head chirp">Chirp Feed</div>
    <div class="abs tweet" style="top:56px"><div class="avatar" role="img" aria-label="Follower avatar" style="background:linear-gradient(135deg,#e8d8c8,#b88a68)"></div><p><b>Joh Mark</b> @ Aliquam nec erat at purus cursus interdum Vestibu-lum ligula augue bibendum<br><small>2 hours ago</small></p></div>
    <div class="abs tweet" style="top:128px"><div class="avatar" role="img" aria-label="Follower avatar" style="background:linear-gradient(135deg,#e0e4e8,#6a4a38)"></div><p><b>Sillon</b> @ Aliquam nec erat at purus cursus interdum Vestibu-lum ligula augue bibendum<br><small>2 hours ago</small></p></div>
    <div class="abs tweet" style="top:203px"><div class="avatar" role="img" aria-label="Follower avatar" style="background:linear-gradient(135deg,#d8dadc,#8a6a58)"></div><p><b>Sillon</b> @ Aliquam nec erat at purus cursus interdum Vestibu-lum ligula augue bibendum<br><small>2 hours ago</small></p></div>
  </section>

  <footer class="abs footer">
    <div class="abs fnav">HOME &nbsp;|&nbsp; ABOUT &nbsp;|&nbsp; LISTEN &nbsp;|&nbsp; SHOWS &nbsp;|&nbsp; BLOG &nbsp;|&nbsp; SUPPORT &nbsp;|&nbsp; CONTACT</div>
    <div class="abs copy">© 2014 Company Name&nbsp; All right reserved&nbsp; Term of Use</div>
    <div class="abs partner">OrbitalWave</div>
  </footer>
</div>
</body>
</html>
```